Homepage for the brisk-find Web Application

At the end of this text, you will find a link to a website that is under construction for a webApp that I intend to launch soon. The contest goal is for you to make redesign the homepage in a nice, fresh, modern Style. Only design, no coding necessary. It needs to have a responsive version for small screens like smart phones. Attached is the text for it, and some images that you may use. You are welcome to find or create additional supporting images. You can use PixTrove.example or similar service to find new images as long as I can purchase the non-exclusive use rights for the images at similar prices. The contest is just for the home page. However, the winner, if I like the work and we can agree on a fair price, could be contracted on a one-on-one basis to do the rest of the site. You are welcome to suggest minor changes like font sizes and minor variations on the Header banner, but that banner is consistent with the user interface of the application therefore should not change too much. The information should flow somewhat continually without much use of side bars or things like that.
https://www.brisk-find.example
Sincerely,
Marco D. Ferral

```html
<!DOCTYPE html>
<html lang="en">
<head>
<meta charset="utf-8">
<title>Brisk Find – Home</title>
<link rel="stylesheet" href="https://fonts.googleapis.com/css2?family=Roboto:wght@400;500;700&family=Roboto+Mono:wght@700&display=swap">
<style>
  :root {
    --blue-dark: #2a6fb8;
    --blue-light: #4b9be0;
    --cyan-soft: #d6f4f8;
    --orange: #e8662f;
    --teal: #2fb3c4;
    --text: #5a5a5a;
    --ink: #1d1d1d;
    --white: #ffffff;
    --sand: #ead8cc;
  }
  * { margin: 0; padding: 0; box-sizing: border-box; }
  html, body { width: 1200px; height: 3872px; overflow: hidden; }
  body {
    position: relative;
    background: var(--white);
    font-family: "Roboto", sans-serif;
    color: var(--text);
  }
  .blob { position: absolute; left: 0; width: 1200px; }
  .site-header {
    position: absolute; top: 0; left: 0; width: 1200px; height: 120px;
    background: linear-gradient(90deg, var(--blue-dark), var(--blue-light));
  }
  .brand {
    position: absolute; left: 20px; top: 22px; display: flex; align-items: center; gap: 14px;
    font-size: 58px; font-weight: 500; color: var(--white); letter-spacing: 1px;
  }
  .brand-dot { width: 74px; height: 74px; border-radius: 50%; background: var(--white); }
  .menu-icon { position: absolute; right: 36px; top: 40px; width: 50px; }
  .menu-icon span { display: block; height: 8px; background: var(--white); margin-bottom: 9px; border-radius: 2px; }
  .menu-note {
    position: absolute; left: 700px; top: 168px; width: 330px; text-align: center;
    font-family: "Roboto Mono", monospace; font-weight: 700; font-size: 28px; line-height: 40px; color: var(--ink);
  }
  .note-arrow { position: absolute; left: 880px; top: 70px; }
  .hero-art {
    position: absolute; left: 70px; top: 130px; width: 500px; height: 680px;
    border-radius: 46% 54% 40% 60% / 38% 42% 58% 62%;
    background: linear-gradient(160deg, #f08a54 0%, var(--sand) 35%, #9fd8e8 70%, #5fb8d4 100%);
  }
  .hero-title {
    position: absolute; left: 590px; top: 320px; width: 580px; text-align: center;
    font-size: 58px; font-weight: 500; line-height: 70px; color: var(--orange); letter-spacing: 2px;
  }
  .divider { position: absolute; left: 512px; top: 848px; width: 176px; height: 8px; background: var(--orange); }
  .section { position: absolute; left: 130px; width: 940px; }
  .section-title {
    text-align: center; color: var(--orange); font-weight: 500;
    font-size: 44px; line-height: 60px; letter-spacing: 2px;
  }
  .section-copy { font-size: 28px; line-height: 46px; letter-spacing: 2px; margin-top: 16px; }
  .section-copy strong { color: var(--ink); font-weight: 700; display: block; }
  .benefits { list-style: none; font-size: 28px; line-height: 46px; letter-spacing: 2px; margin-top: 24px; }
  .benefits li { margin-bottom: 18px; padding-left: 36px; position: relative; }
  .benefits li::before { content: "•"; position: absolute; left: 0; }
  .btn {
    position: absolute; display: flex; align-items: center; justify-content: center;
    height: 96px; border-radius: 48px; background: var(--teal); color: var(--white);
    font-size: 38px; font-weight: 500; letter-spacing: 3px;
    box-shadow: 0 18px 26px rgba(0,0,0,0.25);
  }
  .site-footer {
    position: absolute; left: 0; top: 3792px; width: 1200px; height: 80px;
    background: var(--blue-dark); color: var(--white); font-size: 18px; font-weight: 500;
    display: flex; align-items: center; justify-content: space-between; padding: 0 28px; letter-spacing: 1px;
  }
</style>
</head>
<body>

<svg class="blob" style="top:0" width="1200" height="860" viewBox="0 0 1200 860" aria-hidden="true">
  <path fill="var(--cyan-soft)" d="M0 120 H1200 V560 C1080 620 940 520 820 600 C700 690 600 820 420 800 C240 780 120 700 0 720 Z"/>
</svg>
<svg class="blob" style="top:940px" width="1200" height="720" viewBox="0 0 1200 720" aria-hidden="true">
  <path fill="var(--cyan-soft)" d="M150 60 C300 0 520 40 700 20 C880 0 1060 60 1080 220 C1100 380 1000 520 860 590 C700 670 480 640 320 600 C170 560 90 440 100 300 C110 180 60 110 150 60 Z"/>
</svg>
<svg class="blob" style="top:1640px" width="1200" height="800" viewBox="0 0 1200 800" aria-hidden="true">
  <path fill="var(--cyan-soft)" d="M0 180 C200 60 420 40 640 60 C860 80 1080 20 1200 110 V720 C1000 780 760 700 540 730 C320 760 140 760 0 700 Z"/>
</svg>
<svg class="blob" style="top:2720px" width="1200" height="780" viewBox="0 0 1200 780" aria-hidden="true">
  <path fill="var(--cyan-soft)" d="M0 140 C180 40 400 20 620 40 C840 60 1040 0 1200 80 V700 C1020 760 820 700 600 740 C380 780 180 760 0 700 Z"/>
</svg>

<header class="site-header">
  <div class="brand"><span class="brand-dot"></span>Brisk Find</div>
  <div class="menu-icon" aria-label="Menu"><span></span><span></span><span></span></div>
</header>

<svg class="note-arrow" width="300" height="110" viewBox="0 0 300 110" aria-hidden="true">
  <path d="M10 100 C20 40 120 20 240 28" fill="none" stroke="var(--ink)" stroke-width="6" stroke-linecap="round"/>
</svg>
<p class="menu-note">menu and login<br>will be in here</p>

<div class="hero-art" role="img" aria-label="Illustration of a person searching inside a giant smartphone filled with files"></div>
<h1 class="hero-title">Find that document or item instantly.</h1>

<div class="divider"></div>

<section class="section" style="top:960px">
  <h2 class="section-title">Keeping track of all your paper documents and other belongings has never been easier.</h2>
  <p class="section-copy">Brisk-find is a system that allows you to quickly search for the location of every item that you store or file. It is an essential tool for keeping track of paper documents. In addition, it is incredibly valuable for storing any other kind of physical items. Giving you the ability to quickly find any item, even years after it has been stored. More importantly, using Brisk-find along with some best practice techniques, could allow you to save considerable space without losing fast accessibility of your items.</p>
</section>

<section class="section" style="top:1730px">
  <h2 class="section-title">Why use a storage management system like Brisk-Find?</h2>
  <p class="section-copy"><strong>Managing paper documents</strong>It is quite common for most people and businesses to receive a variety of such documents that need to be filed. The problem is how to efficiently do it in a way that any of it can easily be found, even in a distant future. We normally put them in folders on file drawers sorted by some criteria. But which criterion is the right standard for all kinds of documents? There is no right criterion for every kind of document.</p>
</section>

<a class="btn" style="left:440px; top:2456px; width:320px;">read more</a>

<section class="section" style="top:2790px">
  <h2 class="section-title" style="font-size:58px; line-height:72px;">Why Brisk-Find?</h2>
  <ul class="benefits">
    <li>It is extremely easy to use.</li>
    <li>It is Versatile. Since each catalog can have 1 or many levels of depth (folders and sub-folders). Brisk-find does not force you to use a specific filing or storage methodology.</li>
    <li>It is really affordable. Checkout our pricing plans.</li>
    <li>Since it is online, your data is available almost anywhere in the world.</li>
    <li>Your data always travels encrypted.</li>
  </ul>
</section>

<a class="btn" style="left:368px; top:3462px; width:464px;">start 30 days trial</a>
<a class="btn" style="left:368px; top:3618px; width:464px;">check our pricing</a>

<footer class="site-footer">
  <span>-- contact --</span>
  <span>Copyright © 2016 Lumen Ledger LLC</span>
  <span>-- social media --</span>
</footer>

</body>
</html>
```